WP website design (Tarnwick)

We need a wordpress design for an established auction and real estate company based in Arkansas. The winning design will incorporate a professional color scheme with company logo in a clean layout. The design needs to consider that this will be developed on a responsive theme.

Industry/Entity Type

Real Estate

Font styles to use
Sans Serif

Colors

Designer to choose colors to be used in the design.

Requirements
Must have
• Site will have slideshow, please use stock real estate or other image. A rough idea of homepage content is attached - not necessarily for design purposes.

Navigation Structure is:
1) Home
2) Auctions
3) Services
4) For Sale
5) About Us
6) Ned Videos
7) News & Events
8) Contact Us

Widgets will include:
Social media icons (Facebook, Youtube, RSS)
Testimonials Widget - this should be prominent
Featured Video
Email Signup form (Sign up to receive exclusive email updates for Tarnwick auctions. )
Nice to have
• A drop down menu example
Should not have
• no gavel in the design

```html
<!DOCTYPE html>
<html lang="en">
<head>
<meta charset="utf-8">
<title>Tarnwick Auction &amp; Marketing</title>
<link href="https://fonts.googleapis.com/css2?family=Arimo:wght@400;700&display=swap" rel="stylesheet">
<style>
:root{
  --green:#0b7a3a;
  --green-dark:#06662f;
  --black:#000;
  --ink:#222;
  --muted:#777;
  --band:#e6e6e6;
  --line:#d6d6d6;
  --mint:#55e39a;
  --sky:#29b6d9;
  --amber:#ffb800;
  --footer:#1b1e22;
}
*{box-sizing:border-box;margin:0;padding:0}
html,body{width:1000px;height:1200px;overflow:hidden}
body{position:relative;background:#fff;font-family:"Arimo",Arial,sans-serif;color:var(--ink)}
.abs{position:absolute}
.top-strip{left:0;top:0;width:1000px;height:8px;background:var(--green)}
.brand{left:166px;top:28px}
.brand-name{display:flex;align-items:center;gap:8px;font-size:34px;font-weight:700;color:var(--ink);letter-spacing:1px;line-height:1}
.brand-dot{width:14px;height:14px;border-radius:50%;background:var(--green)}
.brand-sub{margin-top:4px;margin-left:10px;font-size:12.5px;color:var(--green);letter-spacing:1px;text-transform:uppercase}
.contact{right:166px;top:22px;text-align:right}
.phone{display:flex;align-items:center;justify-content:flex-end;gap:6px;font-size:17px;font-weight:700;color:var(--green)}
.contact-name{margin-top:12px;font-size:12.5px;color:var(--ink)}
.contact-role{margin-top:4px;font-size:8px;font-weight:700;color:#999}
.nav{left:0;top:93px;width:1000px;height:46px;background:var(--black)}
.nav ul{list-style:none;position:absolute;left:166px;top:0;display:flex;height:46px}
.nav li{font-size:8.5px;color:#fff;height:46px;display:flex;align-items:center;justify-content:center}
.nav li.active{background:var(--green)}
.nav-line{left:0;top:139px;width:1000px;height:4px;background:var(--green)}
.hero{left:0;top:143px;width:1000px;height:261px;background:var(--band)}
.slider{left:166px;top:147px;width:456px;height:245px;border:1px solid #ccc;background:linear-gradient(180deg,#1f3a12 0%,#4f7d1f 45%,#9ccd45 100%)}
.slider .arrow{position:absolute;top:110px;width:30px;height:30px;border-radius:50%;background:rgba(20,20,20,.85)}
.dots{position:absolute;right:9px;bottom:7px;display:flex;gap:4px}
.dots i{width:7px;height:7px;border-radius:50%;background:#fff}
.dots i:first-child{background:var(--green)}
.agent{left:638px;top:147px;width:196px;height:245px;background:#fff;border:1px solid #ccc}
.agent-photo{height:199px;background:linear-gradient(160deg,#e8d7b8,#c9a983 60%,#3a2f28)}
.agent-name{text-align:center;margin-top:11px;font-size:12px;color:var(--green)}
.agent-role{text-align:center;margin-top:3px;font-size:8px;font-weight:700}
.section-title{left:166px;top:420px;font-size:14px;font-weight:700}
.section-title span{color:var(--green)}
.testimonial{left:166px;top:446px;width:459px;height:128px;border:1px solid var(--line);padding:14px 10px 0 9px}
.t-dots{position:absolute;right:26px;top:-6px;display:flex;gap:10px;background:#fff;padding:0 6px}
.t-dots i{width:9px;height:9px;border-radius:50%;background:#ccc}
.t-dots i:first-child{background:#e01b1b}
.t-head{font-size:8px;font-weight:700;margin-left:2px}
.t-lead{margin-top:4px;font-size:9.4px;line-height:12.7px;width:390px}
.t-body{margin-top:10px;font-size:7.6px;line-height:11.6px;color:#555}
.t-author{position:absolute;right:13px;bottom:10px;font-size:7.6px;font-style:italic;font-weight:700;color:#777}
.auctions{left:166px;top:594px;width:460px;height:489px;border:1px solid var(--line)}
.auctions-head{height:32px;background:linear-gradient(#0e8a42,var(--green-dark));color:#fff;font-size:12.5px;padding:9px 17px}
.auction{position:absolute;left:15px;width:430px;border:1px solid #eee;box-shadow:0 1px 2px rgba(0,0,0,.08)}
.auction-bar{height:23px;color:#fff;font-size:11.5px;font-weight:700;padding:5px 11px}
.auction-row{display:flex;padding:8px 9px}
.auction-img{width:117px;height:90px;flex:none}
.auction-text{margin-left:8px;padding-top:7px}
.auction-text h4{font-size:8.8px;font-weight:700;color:#333}
.auction-text p{font-size:7.6px;color:#666;line-height:12px;margin-top:3px}
.auction-text h4+p{margin-bottom:10px}
.more{position:absolute;left:0;bottom:0;width:100%;height:21px;background:var(--green);color:#fff;font-size:9px;text-align:right;padding:5px 19px}
.signup{left:640px;top:418px;width:194px;height:240px;background:linear-gradient(180deg,#a8c3dc,#bcd0cd 60%,#a9bb97)}
.signup-head{height:29px;background:var(--green);color:#fff;font-size:11.5px;padding:8px 8px}
.field{position:absolute;left:6px;width:180px;height:23px;background:rgba(255,255,255,.55);border:1px solid #c7d6e4;font-size:7px;color:#a8b4bf;padding:7px 7px}
.submit{position:absolute;left:133px;top:212px;width:52px;height:23px;border-radius:6px;background:#000;color:#fff;font-size:9px;font-weight:700;text-align:center;padding-top:6px}
.services{left:642px;top:676px;width:187px;height:194px;border:1px solid #e2e2e2;border-top:3px solid var(--green);padding:14px 12px}
.services h3{font-size:12px;font-weight:400;padding-bottom:6px;border-bottom:1px solid #ddd}
.services ul{list-style:none;margin-top:9px}
.services li{display:flex;justify-content:space-between;align-items:center;font-size:8.8px;height:20.7px;padding-left:2px}
.services li span::before{content:"·";color:#888;margin-right:9px}
.plus{width:7px;height:7px;border:1px solid #bbb;font-size:6px;line-height:5px;text-align:center;color:#777}
.video{left:640px;top:893px;width:194px;height:101px;border:1px solid #ddd;background:linear-gradient(90deg,#f4f4f4,#e8e8e8 60%,#d9c7b5)}
.play{position:absolute;left:83px;top:36px;width:30px;height:30px}
.partners{left:640px;top:1017px;width:194px;height:66px;border:1px solid #d5d5d5;display:flex;align-items:center;justify-content:space-around;padding:0 10px}
.badge{height:18px;background:#d6dbe2;border-radius:3px}
.footer-line{left:0;top:1122px;width:1000px;height:4px;background:var(--green)}
.footer{left:0;top:1126px;width:1000px;height:74px;background:var(--footer)}
.footer-links{position:absolute;left:167px;top:22px;font-size:7.8px;color:#ddd}
.copy{position:absolute;left:166px;top:44px;font-size:7.8px;color:#ddd}
.social{position:absolute;left:721px;top:20px;display:flex;gap:4px}
.social i{width:25px;height:25px;border-radius:4px}
</style>
</head>
<body>
<div class="abs top-strip"></div>

<div class="abs brand">
  <div class="brand-name">TARNWICK <span class="brand-dot"></span></div>
  <div class="brand-sub">Auction &amp; Marketing, LLC</div>
</div>

<div class="abs contact">
  <div class="phone">
    <svg width="30" height="24" viewBox="0 0 30 24" aria-hidden="true"><path d="M3 9c0-5 24-5 24 0v3h-6V9H9v3H3z" fill="#1f63b5"/><rect x="6" y="12" width="18" height="10" rx="3" fill="#2a7be0"/><circle cx="15" cy="17" r="3" fill="#fff"/></svg>
    501 555 0148
  </div>
  <div class="contact-name">Carl Whitby</div>
  <div class="contact-role">Integer sed porta quam</div>
</div>

<nav class="abs nav">
  <ul>
    <li class="active" style="width:88px">Home</li>
    <li style="width:72px">Auctions</li>
    <li style="width:74px">Services</li>
    <li style="width:72px">For Sale</li>
    <li style="width:75px">About Us</li>
    <li style="width:80px">Ned Videos</li>
    <li style="width:89px">News &amp; Events</li>
    <li style="width:62px">Contact Us</li>
  </ul>
</nav>
<div class="abs nav-line"></div>

<div class="abs hero"></div>
<div class="abs slider" role="img" aria-label="Slideshow photo: paper house held over green grass">
  <span class="arrow" style="left:11px"><svg width="30" height="30"><path d="M17 9l-6 6 6 6" stroke="#fff" stroke-width="2.5" fill="none"/></svg></span>
  <span class="arrow" style="right:8px"><svg width="30" height="30"><path d="M13 9l6 6-6 6" stroke="#fff" stroke-width="2.5" fill="none"/></svg></span>
  <div class="dots"><i></i><i></i><i></i></div>
</div>

<div class="abs agent">
  <div class="agent-photo" role="img" aria-label="Portrait photo of the agent"></div>
  <div class="agent-name">Dean Holloway</div>
  <div class="agent-role">Integer sed porta quam</div>
</div>

<h2 class="abs section-title">Customer <span>Testimonials</span></h2>
<div class="abs testimonial">
  <div class="t-dots"><i></i><i></i><i></i><i></i></div>
  <p class="t-head">Integer sed porta quam</p>
  <p class="t-lead">Integer sed porta quam. Suspendisse euismod, risus ac tempus aliquam, quam neque adipiscing lectus, venenatis vestibulum , venenatis. Integer sed orci tellus. Nunc at leo rutrum dolor rhoncus auctor sit amet ac diam. Nunc at metus ante... &nbsp;→</p>
  <p class="t-body">Integer sed porta quam. Suspendisse euismod, risus ac tempus aliquam, quam neque adipiscing lectus, venenatis vestibulum , venenatis.</p>
  <p class="t-author">Laura Pryce</p>
</div>

<section class="abs auctions">
  <div class="auctions-head">CURRENT AUCTIONS</div>

  <div class="auction" style="top:38px">
    <div class="auction-bar" style="background:var(--mint)">Real Estate Auction</div>
    <div class="auction-row">
      <div class="auction-img" role="img" aria-label="Photo: hands holding a model house" style="background:linear-gradient(135deg,#3a2a20,#d98a4a 55%,#f2e2cf)"></div>
      <div class="auction-text">
        <h4>Ridgeway Tourer 2013</h4><p>Integer sed porta quam</p>
        <h4>Ridgeway Tourer 2013</h4><p>Integer sed porta quam. Suspendisse euismod, risus ac tempus aliquam, quam neque adipiscing lectus, venenatis vestibulum , venenatis.</p>
      </div>
    </div>
  </div>

  <div class="auction" style="top:178px">
    <div class="auction-bar" style="background:var(--sky)">Estate Auction</div>
    <div class="auction-row">
      <div class="auction-img" role="img" aria-label="Photo: house with a for-sale sign" style="background:linear-gradient(180deg,#c6d8ea,#e8e4dc 55%,#5f8a3a)"></div>
      <div class="auction-text">
        <h4>Ridgeway Tourer 2013</h4><p>Integer sed porta quam</p>
        <h4>Ridgeway Tourer 2013</h4><p>Integer sed porta quam. Suspendisse euismod, risus ac tempus aliquam, quam neque adipiscing lectus, venenatis vestibulum , venenatis.</p>
      </div>
    </div>
  </div>

  <div class="auction" style="top:321px">
    <div class="auction-bar" style="background:var(--amber)">Automobile Auction</div>
    <div class="auction-row">
      <div class="auction-img" role="img" aria-label="Photo: mechanics working on a car" style="background:linear-gradient(135deg,#5a4a3c,#8a2a2a 50%,#3a3a3a)"></div>
      <div class="auction-text">
        <h4>Ridgeway Tourer 2013</h4><p>Integer sed porta quam</p>
        <h4>Ridgeway Tourer 2013</h4><p>Integer sed porta quam. Suspendisse euismod, risus ac tempus aliquam, quam neque adipiscing lectus, venenatis vestibulum , venenatis.</p>
      </div>
    </div>
  </div>

  <div class="more">More +</div>
</section>

<form class="abs signup">
  <div class="signup-head">Email / Signup form</div>
  <div class="field" style="top:39px">Name</div>
  <div class="field" style="top:69px">Email</div>
  <div class="field" style="top:100px">Mobile</div>
  <div class="field" style="top:130px">City / State</div>
  <div class="field" style="top:160px;height:43px;padding-top:6px">Message</div>
  <div class="submit">Submit</div>
</form>

<aside class="abs services">
  <h3>Services</h3>
  <ul>
    <li><span>House</span><i class="plus">+</i></li>
    <li><span>Automobiles</span><i class="plus">+</i></li>
    <li><span>Rent</span><i class="plus">+</i></li>
    <li><span>House</span><i class="plus">+</i></li>
    <li><span>House</span><i class="plus">+</i></li>
    <li><span>House</span><i class="plus">+</i></li>
  </ul>
</aside>

<div class="abs video" role="img" aria-label="Featured video still: woman working at a laptop">
  <svg class="play" viewBox="0 0 30 30" aria-hidden="true"><circle cx="15" cy="15" r="14" fill="#111" stroke="#fff" stroke-width="2"/><path d="M12 9l9 6-9 6z" fill="#fff"/></svg>
</div>

<div class="abs partners">
  <span class="badge" style="width:38px"></span>
  <span class="badge" style="width:44px;height:24px"></span>
  <span class="badge" style="width:64px"></span>
</div>

<div class="abs footer-line"></div>
<footer class="abs footer">
  <div class="footer-links">Home &nbsp;|&nbsp; About us &nbsp;|&nbsp; Counselling &nbsp;|&nbsp; Workshop &nbsp;|&nbsp; Contact us</div>
  <div class="copy">Content copyright 2013. Tarnwick. All rights reserved.</div>
  <div class="social">
    <i style="background:#3b5a9a"></i>
    <i style="background:#3fa9e0"></i>
    <i style="background:#b52a25"></i>
    <i style="background:#f0831e"></i>
  </div>
</footer>
</body>
</html>
```